Business card for my new company (Accounting firm)

I need a business card for my new business Brightwell Advisory and Ledger SA. Our services are accounting, tax, audit and financial management. Our customers are small companies, start-ups and new companies. The final design has to show financial security, trust and growth. Please find our logo attached to the business card. Text for the business card: Brightwell Advisory and Ledger SA Tomas Varenholt Director and Founder Certified Accountant Tel. 022 418 57 34 tv@clairevalconseil.ch www.clairevalconseil.ch Rue des Vergières 27 1201 Geneva
Target Market(s)
Our customers are small companies, start-ups and new companies.
Industry/Entity Type
Finance And Accounting
Contact Information for Business Card
Claireval Conseil et Comptes SA
Tomas Varenholt
Directeur et Fondateur
Expert-comptable diplômé
Tél. 022 418 57 34
tv@clairevalconseil.ch
www.clairevalconseil.ch
Rue des Vergières 27
1201 Genève

```html
<!DOCTYPE html>
<html lang="fr">
<head>
<meta charset="utf-8">
<title>Claireval Conseil et Comptes SA – Carte de visite</title>
<link rel="stylesheet" href="https://fonts.googleapis.com/css2?family=Roboto:wght@400;500;700&display=swap">
<style>
  :root {
    --backdrop: #3b3c3e;
    --card: #1d1e21;
    --card-edge: #26272b;
    --blue: #2f9ad8;
    --blue-deep: #1f78b8;
    --blue-light: #37ade8;
    --white: #f4f6f8;
    --emboss: #2b2c30;
    --emboss-light: #35363b;
  }
  * { box-sizing: border-box; margin: 0; padding: 0; }
  html, body { width: 799px; height: 1200px; overflow: hidden; }
  body {
    background: var(--backdrop);
    font-family: "Roboto", Arial, sans-serif;
    position: relative;
  }
  .card {
    position: absolute;
    left: 90px;
    width: 620px;
    height: 354px;
    background: var(--card);
    border-radius: 3px;
    overflow: hidden;
    box-shadow: 0 18px 40px rgba(0,0,0,.45);
  }
  .card--front { top: 150px; }
  .card--back { top: 700px; }

  /* front */
  .front-band {
    position: absolute; left: 0; right: 0; bottom: 0; height: 16px;
    background: linear-gradient(90deg, var(--blue-deep), var(--blue-light));
  }
  .front-name {
    position: absolute; left: 0; right: 0; top: 138px;
    text-align: center;
    font-weight: 700; font-size: 34px; letter-spacing: 2px;
    color: var(--emboss-light);
    text-shadow: 0 1px 0 #151619;
  }
  .front-name .mark {
    display: inline-block; width: 18px; height: 18px;
    background: var(--emboss-light); border-radius: 50%;
    margin-right: 14px; vertical-align: 4px;
  }
  .front-sub {
    position: absolute; left: 0; right: 0; top: 186px;
    text-align: center;
    font-weight: 700; font-size: 15px; letter-spacing: 4px;
    color: var(--emboss-light);
  }

  /* back */
  .brand {
    position: absolute; left: 34px; top: 92px; width: 250px;
    text-align: center; color: var(--white);
    font-weight: 700;
  }
  .brand .mark {
    display: block; width: 34px; height: 34px; margin: 0 auto 14px;
    background: var(--blue); border-radius: 50%;
  }
  .brand-name { font-size: 30px; letter-spacing: 2px; line-height: 1; }
  .brand-sub { font-size: 12px; letter-spacing: 3px; margin-top: 8px; }

  .person {
    position: absolute; left: 330px; top: 86px; color: var(--white);
  }
  .person-name { color: var(--blue); font-weight: 700; font-size: 21px; margin-bottom: 8px; }
  .person-role { font-size: 13px; line-height: 1.35; }
  .contacts { list-style: none; margin-top: 18px; }
  .contacts li {
    display: flex; align-items: center; gap: 12px;
    font-size: 14px; line-height: 1; margin-bottom: 9px;
  }
  .contacts svg { width: 12px; height: 12px; flex: none; }

  .back-band {
    position: absolute; left: 0; right: 0; bottom: 0; height: 108px;
    background: linear-gradient(90deg, var(--blue-deep), var(--blue-light));
  }
  .back-band::before {
    content: ""; position: absolute; left: 0; right: 0; top: 8px; height: 1px;
    background: var(--card);
  }
  .address {
    position: absolute; left: 40px; top: 50px; width: 250px;
    text-align: center; color: var(--white); font-size: 15px;
  }
</style>
</head>
<body>

<section class="card card--front" aria-label="Recto">
  <div class="front-name"><span class="mark"></span>CLAIREVAL</div>
  <div class="front-sub">CONSEIL ET COMPTES</div>
  <div class="front-band"></div>
</section>

<section class="card card--back" aria-label="Verso">
  <div class="brand">
    <span class="mark"></span>
    <div class="brand-name">CLAIREVAL</div>
    <div class="brand-sub">CONSEIL ET COMPTES</div>
  </div>

  <div class="person">
    <div class="person-name">Tomas Varenholt</div>
    <div class="person-role">Directeur et Fondateur<br>Expert-comptable diplômé</div>
    <ul class="contacts">
      <li>
        <svg viewBox="0 0 12 12" aria-hidden="true"><path fill="#2f9ad8" d="M1 4c0-2 2-3 5-3s5 1 5 3v1H8.5V4h-5v1H1zM3 6h6l1.5 5h-9z"/></svg>
        022 418 57 34
      </li>
      <li>
        <svg viewBox="0 0 12 12" aria-hidden="true"><rect x="0.5" y="2" width="11" height="8" fill="#2f9ad8"/><path d="M0.5 2l5.5 4.5L11.5 2" fill="none" stroke="#1d1e21" stroke-width="1"/></svg>
        tv@clairevalconseil.ch
      </li>
      <li>
        <svg viewBox="0 0 12 12" aria-hidden="true"><circle cx="6" cy="6" r="5.3" fill="#2f9ad8"/><path d="M0.7 6h10.6M6 0.7v10.6M6 0.7c-3 3-3 7.6 0 10.6M6 0.7c3 3 3 7.6 0 10.6" fill="none" stroke="#1d1e21" stroke-width=".8"/></svg>
        www.clairevalconseil.ch
      </li>
    </ul>
  </div>

  <div class="back-band">
    <div class="address">Rue des Vergières 27 1201 Genève</div>
  </div>
</section>

</body>
</html>
```